Business Card Design Project - del varosi group

dear Sirs

we need business card design for our group ( DEL Varosi Group ) , i have got the Logo design of our group from pixel harbor in previous , so all need details relating to our group i think available with you, as well as the the chosen logo design

we hope to provide us with business card logo that to be appropaite and satisfactory to us .

thanks

note : logo design of our group is attached .
Updates

Reason: please extend the deadline of my project for additional 15 days because i didn't received appropriate design for our gruop yet . kindly beaware that i have received 77 design till now , supossed to send me 200-250 design at least . thanks

Target Market(s)

contents

name : Kerem EL Nadiri

position : Operation Manager

Industry/Entity Type

Business

Requirements
Must have

• person name

group logo
Nice to have
• logo color matching with back background

```html
<!DOCTYPE html>
<html lang="en">
<head>
<meta charset="utf-8">
<title>DEL Varosi Group – Business Card</title>
<link rel="stylesheet" href="https://fonts.googleapis.com/css2?family=Open+Sans:ital,wght@0,400;0,600;1,400&family=Montserrat:wght@500&display=swap">
<style>
  :root {
    --backdrop: #efe8d4;
    --gold-light: #e9bf55;
    --gold: #d2a13a;
    --gold-dark: #b88627;
    --navy: #1f3d7a;
    --ink: #3a3a3a;
    --paper: #ffffff;
  }
  * { margin: 0; padding: 0; box-sizing: border-box; }
  html, body { width: 1200px; height: 951px; overflow: hidden; }
  body {
    background: var(--backdrop);
    position: relative;
    font-family: "Open Sans", Arial, sans-serif;
  }
  .card {
    position: absolute;
    width: 580px;
    height: 330px;
    border-radius: 22px;
    overflow: hidden;
    box-shadow: 0 8px 20px rgba(0,0,0,0.18);
  }
  /* Front side */
  .card-front {
    left: 110px; top: 110px;
    background: linear-gradient(135deg, var(--gold-light) 0%, var(--gold) 55%, var(--gold-dark) 100%);
  }
  .front-accent-area {
    position: absolute; right: 0; top: 0;
    width: 300px; height: 160px;
    background: radial-gradient(ellipse at 100% 0%, rgba(247,227,166,0.45) 0%, rgba(247,227,166,0) 70%);
  }
  .wordmark {
    position: absolute;
    font-family: "Montserrat", Arial, sans-serif;
    font-weight: 500;
    color: var(--navy);
    letter-spacing: 1px;
    display: flex;
    align-items: center;
    gap: 12px;
    white-space: nowrap;
  }
  .wordmark-square {
    width: 18px; height: 18px;
    background: var(--navy);
    flex: none;
  }
  .card-front .wordmark { left: 60px; top: 140px; font-size: 40px; }
  .card-front .wordmark-square { width: 26px; height: 26px; }

  /* Back side */
  .card-back {
    left: 510px; top: 510px;
    background: var(--paper);
  }
  .edge-band {
    position: absolute; top: 0; bottom: 0; width: 16px;
    background: linear-gradient(180deg, var(--gold-light), var(--gold-dark));
  }
  .edge-band.left { left: 0; }
  .edge-band.right { right: 0; }
  .card-back .wordmark { left: 140px; top: 50px; font-size: 30px; }
  .name-bar {
    position: absolute;
    right: 16px; top: 150px;
    width: 250px; height: 62px;
    background: var(--gold);
    color: var(--paper);
    padding: 8px 0 0 28px;
  }
  .person-name { font-size: 19px; letter-spacing: 0.5px; }
  .person-role { font-size: 14px; font-style: italic; }
  .contact-list {
    position: absolute; left: 40px; top: 232px;
    list-style: none;
    font-size: 15px; line-height: 20px; color: var(--ink);
  }
  .contact-list li { display: flex; align-items: center; gap: 10px; }
  .contact-list svg { flex: none; }
  .accent { color: var(--gold); }
  .address {
    position: absolute; left: 330px; top: 250px;
    display: flex; gap: 10px;
    font-size: 15px; line-height: 20px; color: var(--ink);
  }
</style>
</head>
<body>

<section class="card card-front" aria-label="Card front">
  <div class="front-accent-area" role="img" aria-label="Soft light decorative sweep in the top corner"></div>
  <div class="wordmark"><span class="wordmark-square"></span><span>DEL Varosi Group</span></div>
</section>

<section class="card card-back" aria-label="Card back">
  <div class="edge-band left"></div>
  <div class="edge-band right"></div>
  <div class="wordmark"><span class="wordmark-square"></span><span>DEL Varosi Group</span></div>

  <div class="name-bar">
    <div class="person-name">Kerem EL Nadiri</div>
    <div class="person-role">Operation Manager</div>
  </div>

  <ul class="contact-list">
    <li><svg width="12" height="12" viewBox="0 0 12 12"><path d="M3 1 L5 3 L4 5 Q5 7 7 8 L9 7 L11 9 L9 11 Q3 10 1 3 Z" fill="#d2a13a"/></svg><span>512-555-0142</span></li>
    <li><svg width="12" height="12" viewBox="0 0 12 12"><rect x="2" y="5" width="8" height="6" fill="#d2a13a"/><rect x="3" y="1" width="6" height="4" fill="none" stroke="#d2a13a"/></svg><span>512-555-0143</span></li>
    <li><svg width="12" height="12" viewBox="0 0 12 12"><rect x="1" y="3" width="10" height="7" fill="#d2a13a"/><path d="M1 3 L6 7 L11 3" stroke="#fff" fill="none"/></svg><span>info@<span class="accent">delvarosigroup</span>.com</span></li>
    <li><svg width="12" height="12" viewBox="0 0 12 12"><circle cx="6" cy="6" r="5" fill="#d2a13a"/></svg><span>www.<span class="accent">delvarosigroup</span>.com</span></li>
  </ul>

  <div class="address">
    <svg width="14" height="14" viewBox="0 0 14 14" style="margin-top:3px"><path d="M7 1 L13 7 L11 7 L11 13 L3 13 L3 7 L1 7 Z" fill="#d2a13a"/></svg>
    <div>4100 Lane Oak Blvd.<br>Suite 210-340<br>Marlow, TX 78115</div>
  </div>
</section>

</body>
</html>
```